Business Card, A4 Letter Head and DL Envelope for Brandvelle

We are looking for a design for our Business Card, A4 Letter Head and DL Envelope.

Brandvelle is a distributor of promotional products. We specialize in a range of branded promotional products, these include pens, polo shirts, key rings, drink bottles, uniforms and bags to name a few. We are experts in marketing and assist companies in choosing the right promotional product for their needs. We will predominately be an online business where customers visit our website and browse our range of promotional products and branding options.

Our colours are black, red, white and grey.

Files must be supplied in eps, pdf and ai format.

Please display the following information:
Derek Halloway
Account Manager
Suite xxx, 212 Ferrow Lane Melbourne, Victoria 3000
Phone +61 3 5550 1827
Mobile +61 455 016 342
sales@brandvelle-example.com.au
www.brandvelle-example.com.au

```html
<!DOCTYPE html>
<html lang="en">
<head>
<meta charset="utf-8">
<title>Brandvelle Stationery</title>
<link href="https://fonts.googleapis.com/css2?family=Exo+2:wght@600;700&family=Open+Sans:wght@400;600;700&display=swap" rel="stylesheet">
<style>
  :root{
    --red:#c8141d;
    --red-deep:#7e0a10;
    --grey:#bdbdbd;
    --grey-dark:#4a4a4a;
    --ink:#111;
    --paper:#fff;
    --backdrop:#e9e6e1;
  }
  *{box-sizing:border-box;margin:0;padding:0}
  html,body{width:1200px;height:1024px;overflow:hidden}
  body{background:var(--backdrop);position:relative;font-family:"Open Sans",sans-serif}
  .piece{position:absolute;overflow:hidden;background:var(--paper);box-shadow:0 3px 10px rgba(0,0,0,.25)}
  .piece > svg.art{position:absolute;inset:0;width:100%;height:100%}
  .rounded{border-radius:16px}
  .wordmark{position:absolute;font-family:"Exo 2",sans-serif;font-weight:700;color:var(--grey-dark);letter-spacing:.5px;display:flex;align-items:center;gap:8px;white-space:nowrap}
  .wordmark .dot{display:inline-block;border-radius:50%;background:var(--red)}
  .wordmark.light{color:var(--paper)}
  .wordmark.light .dot{background:var(--paper)}
  .url{position:absolute;color:var(--paper);font-size:8px;white-space:nowrap}
  .url.red{color:var(--red)}
  .lh-footer{position:absolute;bottom:12px;right:12px;display:flex;gap:12px;color:var(--paper);font-size:5.5px;line-height:1.35;white-space:nowrap}
  .card-name{position:absolute;right:22px;top:42px;text-align:right}
  .card-name h2{font-family:"Exo 2",sans-serif;font-size:14px;color:var(--red-deep);font-weight:700}
  .card-name p{font-size:9px;color:var(--grey-dark)}
  .card-contact{position:absolute;color:var(--paper);font-size:9px;line-height:1.4;white-space:nowrap}
  .env-contact{position:absolute;left:248px;top:24px;font-size:6.5px;line-height:1.35;color:var(--grey-dark)}
  .env-contact b{color:var(--red);font-weight:600}
  .env-window{position:absolute;left:20px;top:100px;width:138px;height:36px;border:1px solid #ccc;border-radius:4px;background:linear-gradient(#f4f4f4,#e2e2e2)}
  .big-mark{position:absolute;border-radius:50%}
  .url-sm{font-size:9px}
</style>
</head>
<body>

<!-- Presentation folder -->
<section class="piece folder" style="left:41px;top:26px;width:351px;height:498px">
  <svg class="art" viewBox="0 0 100 100" preserveAspectRatio="none" aria-hidden="true">
    <defs><linearGradient id="fRed" x1="0" y1="0" x2="0" y2="1"><stop offset="0" stop-color="#d8161f"/><stop offset="1" stop-color="#8a0b11"/></linearGradient></defs>
    <path d="M30 0H100V11C82 4 60 1 30 0Z" fill="url(#fRed)"/>
    <path d="M28 0C60 1 84 5 100 12V13.2C84 6.5 60 2 28 0Z" fill="var(--grey)"/>
    <path d="M0 37C30 43 62 56 100 47V53C62 61 30 50 0 46Z" fill="var(--grey)"/>
    <path d="M0 46C30 50 62 61 100 53V55C62 63 30 52 0 48.5Z" fill="var(--ink)"/>
    <path d="M0 49C30 53 62 64 100 56V100H0Z" fill="url(#fRed)"/>
  </svg>
  <div class="big-mark" style="left:160px;top:300px;width:190px;height:190px;background:rgba(255,255,255,.08)"></div>
  <div class="wordmark" style="left:80px;top:128px;font-size:26px"><span class="dot" style="width:34px;height:34px"></span>BRANDVELLE</div>
  <div class="url" style="left:120px;bottom:14px">www.brandvelle-example.com.au</div>
</section>

<!-- Letterhead, plain -->
<section class="piece letterhead" style="left:419px;top:26px;width:354px;height:498px">
  <svg class="art" viewBox="0 0 100 100" preserveAspectRatio="none" aria-hidden="true">
    <defs><linearGradient id="l1Red" x1="0" y1="0" x2="0" y2="1"><stop offset="0" stop-color="#d8161f"/><stop offset="1" stop-color="#8a0b11"/></linearGradient></defs>
    <path d="M35 0H100V7C82 3 60 1 35 0Z" fill="url(#l1Red)"/>
    <path d="M33 0C60 1 84 3 100 8V9C84 4.5 60 1.5 33 0Z" fill="var(--grey)"/>
    <path d="M0 86C30 90 62 82 100 85V88C62 85 30 92 0 89Z" fill="var(--grey)"/>
    <path d="M0 89C30 92 62 85 100 88V89.3C62 86.5 30 93.5 0 90.5Z" fill="var(--ink)"/>
    <path d="M0 91C30 94 62 87 100 89.5V100H0Z" fill="url(#l1Red)"/>
  </svg>
  <div class="wordmark" style="left:20px;top:58px;font-size:13px"><span class="dot" style="width:16px;height:16px"></span>BRANDVELLE</div>
  <div class="url" style="right:12px;top:6px;font-size:6px">www.brandvelle-example.com.au</div>
  <div class="lh-footer"><div>ABN : 00 000 000 000<br>Suite xxx, 212 Ferrow Lane<br>Melbourne, Victoria 3000</div><div>P : +61 3 5550 1827<br>M : +61 455 016 342<br>E : sales@brandvelle-example.com.au</div></div>
</section>

<!-- Letterhead, with faint decoration -->
<section class="piece letterhead" style="left:805px;top:26px;width:357px;height:498px">
  <svg class="art" viewBox="0 0 100 100" preserveAspectRatio="none" aria-hidden="true">
    <defs><linearGradient id="l2Red" x1="0" y1="0" x2="0" y2="1"><stop offset="0" stop-color="#d8161f"/><stop offset="1" stop-color="#8a0b11"/></linearGradient></defs>
    <path d="M35 0H100V7C82 3 60 1 35 0Z" fill="url(#l2Red)"/>
    <path d="M33 0C60 1 84 3 100 8V9C84 4.5 60 1.5 33 0Z" fill="var(--grey)"/>
    <path d="M0 86C30 90 62 82 100 85V88C62 85 30 92 0 89Z" fill="var(--grey)"/>
    <path d="M0 89C30 92 62 85 100 88V89.3C62 86.5 30 93.5 0 90.5Z" fill="var(--ink)"/>
    <path d="M0 91C30 94 62 87 100 89.5V100H0Z" fill="url(#l2Red)"/>
  </svg>
  <div class="big-mark" style="left:160px;top:255px;width:200px;height:200px;background:rgba(200,20,29,.08)"></div>
  <div class="wordmark" style="left:20px;top:58px;font-size:13px"><span class="dot" style="width:16px;height:16px"></span>BRANDVELLE</div>
  <div class="url" style="right:12px;top:6px;font-size:6px">www.brandvelle-example.com.au</div>
  <div class="lh-footer"><div>ABN : 00 000 000 000<br>Suite xxx, 212 Ferrow Lane<br>Melbourne, Victoria 3000</div><div>P : +61 3 5550 1827<br>M : +61 455 016 342<br>E : sales@brandvelle-example.com.au</div></div>
</section>

<!-- Business card front -->
<section class="piece card rounded" style="left:32px;top:554px;width:360px;height:206px">
  <svg class="art" viewBox="0 0 100 100" preserveAspectRatio="none" aria-hidden="true">
    <defs><linearGradient id="cRed" x1="0" y1="0" x2="0" y2="1"><stop offset="0" stop-color="#d8161f"/><stop offset="1" stop-color="#8a0b11"/></linearGradient></defs>
    <path d="M0 46C30 52 62 40 100 44V52C62 48 30 60 0 54Z" fill="var(--grey)"/>
    <path d="M0 54C30 60 62 48 100 52V54.5C62 50.5 30 62.5 0 56.5Z" fill="var(--ink)"/>
    <path d="M0 57C30 63 62 51 100 55V100H0Z" fill="url(#cRed)"/>
  </svg>
  <div class="wordmark" style="left:20px;top:42px;font-size:17px"><span class="dot" style="width:22px;height:22px"></span>BRANDVELLE</div>
  <div class="card-name"><h2>DEREK HALLOWAY</h2><p>Account Manager</p></div>
  <div class="card-contact" style="left:16px;top:140px">Suite xxx, 212 Ferrow Lane<br>Melbourne, Victoria 3000<br>ABN : 00 000 000 000</div>
  <div class="card-contact" style="left:205px;top:132px;font-size:8.5px">P : +61 3 5550 1827<br>M : +61 455 016 342<br>E : sales@brandvelle-example.com.au<br>W : www.brandvelle-example.com.au</div>
</section>

<!-- Business card backs -->
<section class="piece card rounded" style="left:415px;top:554px;width:367px;height:206px;background:radial-gradient(circle at 55% 45%,#e01a23,#8a0b11 80%)">
  <div class="big-mark" style="left:-10px;top:10px;width:190px;height:190px;background:radial-gradient(circle at 35% 30%,#f2f2f2,#b8b8b8 60%,#8a8a8a)"></div>
  <div class="wordmark light" style="left:196px;top:120px;font-size:17px">BRANDVELLE</div>
  <div class="url url-sm" style="left:206px;top:144px">www.brandvelle-example.com.au</div>
</section>

<section class="piece card rounded" style="left:802px;top:550px;width:372px;height:212px;background:radial-gradient(circle at 40% 45%,#e01a23,#8a0b11 80%)">
  <div class="big-mark" style="left:182px;top:12px;width:186px;height:186px;background:radial-gradient(circle at 35% 30%,#f2f2f2,#b8b8b8 60%,#8a8a8a)"></div>
  <div class="wordmark light" style="left:20px;top:120px;font-size:17px">BRANDVELLE</div>
  <div class="url url-sm" style="left:24px;top:144px">www.brandvelle-example.com.au</div>
</section>

<!-- DL envelope front -->
<section class="piece envelope" style="left:10px;top:792px;width:384px;height:186px">
  <svg class="art" viewBox="0 0 100 100" preserveAspectRatio="none" aria-hidden="true">
    <defs><linearGradient id="eRed" x1="0" y1="0" x2="0" y2="1"><stop offset="0" stop-color="#d8161f"/><stop offset="1" stop-color="#8a0b11"/></linearGradient></defs>
    <path d="M0 70C30 78 62 64 100 68V74C62 70 30 84 0 77Z" fill="var(--grey)"/>
    <path d="M0 77C30 84 62 70 100 74V76C62 72 30 86 0 79Z" fill="var(--ink)"/>
    <path d="M0 80C30 87 62 73 100 77V100H0Z" fill="url(#eRed)"/>
  </svg>
  <div class="wordmark" style="left:22px;top:32px;font-size:14px"><span class="dot" style="width:20px;height:20px"></span>BRANDVELLE</div>
  <div class="env-contact"><b>P :</b> +61 3 5550 1827<br><b>M :</b> +61 455 016 342<br><b>E :</b> sales@brandvelle-example.com.au<br>Suite xxx, 212 Ferrow Lane<br>Melbourne, Victoria 3000</div>
  <div class="env-window"></div>
  <div class="url" style="right:16px;bottom:10px;font-size:7px">www.brandvelle-example.com.au</div>
</section>

<!-- DL envelope back, white -->
<section class="piece envelope" style="left:403px;top:792px;width:390px;height:186px">
  <svg class="art" viewBox="0 0 100 100" preserveAspectRatio="none" aria-hidden="true">
    <defs><linearGradient id="e2Red" x1="0" y1="0" x2="0" y2="1"><stop offset="0" stop-color="#d8161f"/><stop offset="1" stop-color="#8a0b11"/></linearGradient></defs>
    <path d="M28 0H100V18C84 8 60 2 28 0Z" fill="url(#e2Red)"/>
    <path d="M26 0C60 2 84 8 100 19V20C84 10 60 3 26 0Z" fill="var(--grey)"/>
    <path d="M0 0L8 26C9 30 12 32 16 32H84C88 32 91 30 92 26L100 0" fill="none" stroke="#d4d4d4" stroke-width=".5"/>
  </svg>
  <div class="big-mark" style="left:255px;top:40px;width:130px;height:130px;background:rgba(200,20,29,.08)"></div>
  <div class="url red" style="left:150px;bottom:12px;font-size:7px">www.brandvelle-example.com.au</div>
</section>

<!-- DL envelope back, red -->
<section class="piece envelope" style="left:802px;top:792px;width:390px;height:186px;background:radial-gradient(circle at 45% 40%,#e01a23,#8a0b11 85%)">
  <svg class="art" viewBox="0 0 100 100" preserveAspectRatio="none" aria-hidden="true">
    <path d="M0 0L8 26C9 30 12 32 16 32H84C88 32 91 30 92 26L100 0" fill="none" stroke="rgba(0,0,0,.25)" stroke-width=".6"/>
  </svg>
  <div class="wordmark light" style="left:0;right:0;top:10px;justify-content:center;flex-direction:column;gap:3px;font-size:10px"><span class="dot" style="width:14px;height:14px"></span>BRANDVELLE</div>
  <div class="url" style="left:150px;bottom:12px;font-size:7px">www.brandvelle-example.com.au</div>
</section>

</body>
</html>
```